Verodex business card

Business card for sustainable investment company called "Verodex". Verodex is an exchange platform selling carbon credits between buyers and sellers. Carbon Credits are an environmental commodity for reducing global carbon emissions.

the card should obviously have our logo and the theme should be sustainability/environment mixed with a trading platform.

Contact Information for Business Card

Logo, Name, Title, Phone, Email

Colors
0054AA
0677BA
7BADD7
CADEEF
E8F1F8
0094D4
00A9DD
6FCCEA
C7EBF8
E9F6FB
00AB8E
00BBA5
67D7C9
C6EFE9
E9F9F6
59FF00
82FF00
B8FF75
E3FFCB
F4FFEA

```html
<!DOCTYPE html>
<html lang="en">
<head>
<meta charset="utf-8">
<title>Verodex business card</title>
<link rel="stylesheet" href="https://fonts.googleapis.com/css2?family=Montserrat:wght@500;600;700&family=Lato:wght@400;700&display=swap">
<style>
  :root {
    --navy: #1b2a44;
    --slate: #4a5568;
    --bg: #e4e6e9;
    --card: #ffffff;
    --blue-deep: #0677BA;
    --blue: #0094D4;
    --cyan: #00A9DD;
    --aqua: #6FCCEA;
    --rule: #3b4a66;
  }
  * { box-sizing: border-box; margin: 0; padding: 0; }
  html, body {
    width: 1200px; height: 800px; overflow: hidden;
    background: var(--bg);
    font-family: "Lato", Arial, sans-serif;
  }
  .sheet {
    width: 1200px; height: 800px;
    display: flex; align-items: center; justify-content: center; gap: 48px;
  }
  .card {
    position: relative;
    width: 540px; height: 309px;
    background: var(--card);
    overflow: hidden;
    box-shadow: 0 10px 30px rgba(30, 40, 60, 0.12);
  }
  .card__accent {
    position: absolute; top: 0; height: 100%;
  }
  .card--back .card__accent { left: 0; width: 190px; }
  .card--front .card__accent { right: 0; width: 170px; }

  .wordmark {
    font-family: "Montserrat", Arial, sans-serif;
    font-weight: 600;
    color: var(--navy);
    text-transform: uppercase;
    letter-spacing: 0.02em;
  }
  .card--back .wordmark {
    position: absolute; left: 215px; top: 50%;
    transform: translateY(-50%);
    font-size: 50px;
  }
  .brand {
    position: absolute; left: 36px; top: 30px;
    display: flex; align-items: center; gap: 12px;
  }
  .brand__mark {
    width: 30px; height: 30px;
    background: linear-gradient(135deg, var(--aqua), var(--blue-deep));
  }
  .brand .wordmark { font-size: 32px; }

  .contact {
    position: absolute; left: 36px; top: 128px;
  }
  .contact__name {
    font-weight: 700; font-size: 14px; color: var(--navy);
    letter-spacing: 0.04em; text-transform: uppercase;
    display: flex; align-items: center;
  }
  .contact__rule {
    display: inline-block; width: 190px; height: 1px;
    background: var(--rule); margin-left: 8px; margin-top: 8px;
  }
  .contact__title { font-size: 13px; color: var(--slate); margin-top: 2px; }
  .contact__list { list-style: none; margin-top: 14px; }
  .contact__item {
    display: flex; align-items: center; gap: 8px;
    font-size: 13px; color: var(--navy); margin-bottom: 6px;
  }
  .contact__icon { width: 12px; height: 12px; fill: var(--cyan); }
</style>
</head>
<body>
<main class="sheet">

  <section class="card card--front" aria-label="Business card front">
    <svg class="card__accent" viewBox="0 0 170 309" role="img" aria-label="Brand accent panel in blue gradient" preserveAspectRatio="none">
      <defs>
        <linearGradient id="accentFront" x1="0" y1="0" x2="1" y2="1">
          <stop offset="0" stop-color="#6FCCEA"/>
          <stop offset="1" stop-color="#0677BA"/>
        </linearGradient>
      </defs>
      <polygon points="70,0 170,0 170,309 20,309" fill="url(#accentFront)"/>
    </svg>

    <div class="brand">
      <span class="brand__mark" aria-hidden="true"></span>
      <span class="wordmark">Verodex</span>
    </div>

    <div class="contact">
      <p class="contact__name">Daniel Harper<span class="contact__rule" aria-hidden="true"></span></p>
      <p class="contact__title">Director</p>
      <ul class="contact__list">
        <li class="contact__item">
          <svg class="contact__icon" viewBox="0 0 24 24" aria-hidden="true"><path d="M6.6 10.8a15 15 0 0 0 6.6 6.6l2.2-2.2c.3-.3.7-.4 1-.2 1.1.4 2.3.6 3.6.6.6 0 1 .4 1 1V20c0 .6-.4 1-1 1C10.6 21 3 13.4 3 4c0-.6.4-1 1-1h3.5c.6 0 1 .4 1 1 0 1.3.2 2.5.6 3.6.1.3 0 .7-.2 1z"/></svg>
          300-415-7720
        </li>
        <li class="contact__item">
          <svg class="contact__icon" viewBox="0 0 24 24" aria-hidden="true"><path d="M2 5h20v14H2z M2 5l10 8 10-8" /></svg>
          info@verodex.com
        </li>
      </ul>
    </div>
  </section>

  <section class="card card--back" aria-label="Business card back">
    <svg class="card__accent" viewBox="0 0 190 309" role="img" aria-label="Brand accent panel in blue gradient" preserveAspectRatio="none">
      <defs>
        <linearGradient id="accentBack" x1="0" y1="1" x2="1" y2="0">
          <stop offset="0" stop-color="#6FCCEA"/>
          <stop offset="1" stop-color="#0677BA"/>
        </linearGradient>
      </defs>
      <polygon points="0,0 130,0 180,309 0,309" fill="url(#accentBack)"/>
    </svg>
    <h1 class="wordmark">Verodex</h1>
  </section>

</main>
</body>
</html>
```